Corvane Capital Business Cards

These are professional business cards that are for my family office.
Put fake emails and phone numbers as of now until I finalize those components. This family office controls my families investments, assets, and future. The cards should be professional.
..
.
.
.
I just uploaded another variation of a logo I would like to see as a business card to I am inbeteen which logo to use

Target Market(s)

business

Industry/Entity Type

business

Contact Information for Business Card

Professional, wealth related, finance related.

Requirements
Must have
• Logo

```html
<!DOCTYPE html>
<html lang="en">
<head>
<meta charset="utf-8">
<title>Corvane Capital Business Cards</title>
<link rel="stylesheet" href="https://fonts.googleapis.com/css2?family=Cinzel:wght@500&family=Montserrat:wght@400;700&display=swap">
<style>
  :root {
    --stage: #2a2a2c;
    --navy: #1b2132;
    --navy-deep: #151a28;
    --paper: #ffffff;
    --grey: #a9a9a9;
    --ink: #1b2132;
    --muted: #4a4f5c;
  }
  * { box-sizing: border-box; margin: 0; padding: 0; }
  html, body { width: 1200px; height: 875px; overflow: hidden; }
  body {
    background: var(--stage);
    font-family: "Montserrat", Arial, sans-serif;
    position: relative;
  }
  .card {
    position: absolute;
    top: 283px;
    width: 540px;
    height: 309px;
    border-radius: 18px;
    overflow: hidden;
  }
  .card--back { left: 40px; background: var(--navy); }
  .card--front { left: 620px; background: var(--paper); }

  .monogram-field {
    position: absolute; inset: 0;
    background: linear-gradient(120deg, #2a3146 0%, var(--navy) 45%, var(--navy-deep) 100%);
  }
  .back-mark {
    position: absolute; right: 60px; top: 112px;
    display: flex; align-items: center; gap: 10px;
  }
  .back-mark .dot {
    width: 44px; height: 44px; border-radius: 50%;
    border: 2px solid #e8e9ee;
  }
  .back-mark .name {
    font-family: "Cinzel", Georgia, serif; font-weight: 500;
    color: #e8e9ee; font-size: 13px; letter-spacing: 1px;
  }

  .wordmark {
    position: absolute; left: 34px; top: 72px;
    font-family: "Cinzel", Georgia, serif; font-weight: 500;
    font-size: 38px; color: var(--ink); letter-spacing: 0.5px;
  }
  .person { position: absolute; left: 52px; top: 162px; text-align: right; }
  .person .full-name { font-weight: 700; font-size: 17px; color: var(--ink); }
  .person .role { font-size: 10px; color: var(--muted); margin-top: 1px; }
  .divider {
    position: absolute; left: 232px; top: 148px;
    width: 1.5px; height: 60px; background: var(--ink);
  }
  .contacts {
    position: absolute; left: 250px; top: 146px;
    list-style: none; font-size: 10.5px; color: var(--ink);
  }
  .contacts li { display: flex; align-items: center; gap: 7px; height: 20px; }
  .contacts svg { width: 10px; height: 10px; fill: var(--ink); }
  .grey-tab {
    position: absolute; right: 0; top: 186px;
    width: 78px; height: 24px; background: var(--grey);
  }
  .address-band {
    position: absolute; left: 0; top: 236px;
    width: 440px; height: 26px; background: var(--navy);
    color: #ffffff; font-size: 10.5px;
    display: flex; align-items: center; padding-left: 118px;
  }
  .front-mark {
    position: absolute; left: 410px; top: 188px;
    width: 62px; height: 62px; border-radius: 50%;
    background: var(--paper); border: 2.5px solid var(--navy);
  }
</style>
</head>
<body>
  <section class="card card--back" aria-label="Card back">
    <div class="monogram-field" role="img" aria-label="Repeating embossed monogram pattern in dark navy"></div>
    <div class="back-mark">
      <span class="dot"></span>
      <span class="name">Corvane Capital</span>
    </div>
  </section>

  <section class="card card--front" aria-label="Card front">
    <h1 class="wordmark">Corvane Capital</h1>

    <div class="person">
      <p class="full-name">Marcus Ellery</p>
      <p class="role">Owner</p>
    </div>

    <span class="divider"></span>

    <ul class="contacts">
      <li>
        <svg viewBox="0 0 10 10"><path d="M2 0.5 L3.6 0.5 L4.2 2.8 L3 3.6 C3.6 5 4.9 6.4 6.4 7 L7.2 5.8 L9.5 6.4 L9.5 8 C9.5 9 8.7 9.6 7.8 9.5 C4 9 1 6 0.5 2.2 C0.4 1.3 1 0.5 2 0.5 Z"/></svg>
        (555)214-7730
      </li>
      <li>
        <svg viewBox="0 0 10 10"><path d="M0.5 2 H9.5 V8.5 H0.5 Z M1.2 2.6 L5 5.4 L8.8 2.6" stroke="#fff" stroke-width="0.8"/></svg>
        info@corvanecapital.com
      </li>
      <li>
        <svg viewBox="0 0 10 10"><circle cx="5" cy="5" r="4.5"/><path d="M0.5 5 H9.5 M5 0.5 C3 3 3 7 5 9.5 M5 0.5 C7 3 7 7 5 9.5" stroke="#fff" stroke-width="0.7" fill="none"/></svg>
        www.corvanecapital.com
      </li>
    </ul>

    <span class="grey-tab"></span>
    <div class="address-band">48 Alder Court Plaza Fairhaven, NJ 07100 USA</div>
    <span class="front-mark"></span>
  </section>
</body>
</html>
```